Quorva - corporate Business Card

We need a good look and innovative business card for a new start up company based in Los Angeles called "Quorva". We are in a payment business, including payment card, app, and ewallet. We are expert in online payment and Card not present (CNP) transaction.
We need an innovative, modern business card.

Our logo font is Aero Matics

Target Market(s)

Startup - Bank - Online Payment - Card Manufacturing

Industry/Entity Type

Startup

Contact Information for Business Card

phone: 555 014 7396 - Address: 4172 Marlowe blvd, Brenton Falls, OR 97318

Requirements
Must have
• Message: innovative, professional, expert, high tech, trust, online payment expert, security
Nice to have
• no comment
Should not have
• no Comment

```html
<!DOCTYPE html>
<html lang="en">
<head>
<meta charset="utf-8">
<title>Quorva – Business Card</title>
<link rel="stylesheet" href="https://fonts.googleapis.com/css2?family=Exo+2:wght@700&family=Open+Sans:wght@400&display=swap">
<style>
  :root {
    --backdrop: #e6e4e2;
    --card-light: #fdfdfd;
    --card-shade: #efeeee;
    --brand-red: #c0283a;
    --brand-red-deep: #a91f31;
    --ink: #2a2a2a;
    --on-red: #ffffff;
  }
  * { margin: 0; padding: 0; box-sizing: border-box; }
  html, body {
    width: 1200px; height: 900px; overflow: hidden;
    background: var(--backdrop);
  }
  .business-card {
    position: absolute; left: 150px; top: 173px;
    width: 900px; height: 554px;
    border-radius: 25px; overflow: hidden;
    background: linear-gradient(135deg, var(--card-light) 0%, var(--card-shade) 100%);
    box-shadow: 0 10px 30px rgba(0,0,0,0.12);
  }
  .accent-disc {
    position: absolute; left: 523px; top: -24px;
    width: 602px; height: 602px; border-radius: 50%;
    background: linear-gradient(160deg, var(--brand-red) 0%, var(--brand-red-deep) 100%);
  }
  .brand-dot {
    position: absolute; left: 129px; top: 45px;
    width: 138px; height: 138px; border-radius: 50%;
    background: var(--brand-red);
  }
  .brand-name {
    position: absolute; left: 44px; top: 195px;
    font-family: "Exo 2", sans-serif; font-weight: 700;
    font-size: 86px; line-height: 1; letter-spacing: 1px;
    color: var(--brand-red);
  }
  .holder-name {
    position: absolute; left: 44px; top: 372px;
    font-family: "Exo 2", sans-serif; font-weight: 700;
    font-size: 30px; line-height: 1; letter-spacing: 0.5px;
    color: var(--brand-red);
  }
  .holder-role, .postal-address {
    position: absolute; left: 45px;
    font-family: "Open Sans", sans-serif; font-weight: 400;
    font-size: 22px; line-height: 1; color: var(--ink);
    white-space: nowrap;
  }
  .holder-role { top: 406px; }
  .postal-address { left: 48px; top: 467px; }
  .contact-list {
    position: absolute; right: 48px; top: 268px;
    list-style: none;
    font-family: "Open Sans", sans-serif; font-size: 22px;
    color: var(--on-red);
  }
  .contact-item {
    display: flex; align-items: center; justify-content: flex-end;
    gap: 12px; height: 35px; white-space: nowrap;
  }
  .contact-icon { width: 18px; height: 18px; fill: var(--on-red); }
</style>
</head>
<body>
  <div class="business-card">
    <div class="accent-disc"></div>

    <div class="brand-dot"></div>
    <div class="brand-name">quorva</div>

    <div class="holder-name">DANIEL HARWICK</div>
    <div class="holder-role">Managing Director</div>
    <div class="postal-address">4172 Marlowe blvd, Brenton Falls, OR 97318</div>

    <ul class="contact-list">
      <li class="contact-item">
        <span>555 014 7396</span>
        <svg class="contact-icon" viewBox="0 0 24 24" aria-hidden="true">
          <path d="M6.6 10.8a15.1 15.1 0 0 0 6.6 6.6l2.2-2.2c.3-.3.7-.4 1-.2 1.1.4 2.3.6 3.6.6.6 0 1 .4 1 1V20c0 .6-.4 1-1 1A17 17 0 0 1 3 4c0-.6.4-1 1-1h3.5c.6 0 1 .4 1 1 0 1.3.2 2.5.6 3.6.1.3 0 .7-.2 1z"/>
        </svg>
      </li>
      <li class="contact-item">
        <span>www.quorva.com</span>
        <svg class="contact-icon" viewBox="0 0 24 24" aria-hidden="true">
          <path d="M12 2a10 10 0 1 0 0 20 10 10 0 0 0 0-20zm-1 17.9A8 8 0 0 1 4.1 10L9 15v1a2 2 0 0 0 2 2zm6.9-2.5A2 2 0 0 0 16 16h-1v-3a1 1 0 0 0-1-1H8v-2h2a1 1 0 0 0 1-1V7h2a2 2 0 0 0 2-2v-.4a8 8 0 0 1 2.9 12.8z"/>
        </svg>
      </li>
    </ul>
  </div>
</body>
</html>
```